Salmon Shop that sells both wholesale and retail salmon in a variety of ways.

"Reef Harvest" is a business that is selling atlantic salmon in every way possible. We will be a salmon butcher to the public for retail purchase and we will also be out and about trying to sell our products to restaurants cafes and any other wholesale way. Our product is from Tasmania but we will be trading on the Sunshine Coast. The shop design has an urban, rustic feel and very much about the product. One of the owners has worked on salmon farms for 15 years and we want it to be very specialised and quality. I have nothing to offer you to help with this design....I would like both a salmon on the card, not sure if image or silohette is best and would like the other side to have a fillet with a tag of some sort. We are looking for a logo also. Use a photo of an Atlantic Salmon, Atlantic Salmon have two fins along the back.
Updates

Project Deadline Extended Reason: I am extending the deadline as I have still not got exactly what I want. All designers have added something great to what I am after and I just need someone to pull it all together. I have put in a new brief with a sketched image to help so we can get this perfect. Please read all the instructions. Thank you Added Monday, February 16, 2015

Target Market(s)

Restaurants, cafes

Industry/Entity Type

Retail

Contact Information for Business Card

Reef Harvest (Not to have "Shop" at the end.Shop 12/130-164 Brisbane RdMooloolaba 4557

Colors
1c66ab

Requirements
Must have
• logo for reef harvest with the S being salmon fillet of fresh salmon on white platemap of tasmaniasepia /black and white image of atlantic salmon
Nice to have
• fillet of salmonmap of tasmaniasalmon
Should not have
• Not Shop at the end.

```html
<!DOCTYPE html>
<html lang="en">
<head>
<meta charset="utf-8">
<title>Reef Harvest — Business Card</title>
<link rel="stylesheet" href="https://fonts.googleapis.com/css2?family=Questrial&family=Source+Sans+3:wght@400&display=swap">
<style>
  :root {
    --page: #f4f4f2;
    --wood-light: #c9a783;
    --wood-mid: #b8916a;
    --wood-dark: #a67f5a;
    --brand-blue: #1fa9d2;
    --ink: #3b2a1c;
    --photo-cream: #eadcc6;
    --photo-tan: #d9a877;
    --photo-salmon: #c9794a;
    --overlay-white: rgba(255, 255, 255, 0.8);
    --card-shadow: 0 6px 18px rgba(0, 0, 0, 0.22);
  }
  * { box-sizing: border-box; margin: 0; padding: 0; }
  html, body {
    width: 1200px;
    height: 800px;
    overflow: hidden;
    background: var(--page);
  }
  .sheet {
    width: 1200px;
    height: 800px;
    display: flex;
    align-items: center;
    justify-content: center;
    gap: 120px;
  }

  /* Cards stand upright; their content runs along the long edge, reading top to bottom */
  .card {
    position: relative;
    width: 288px;
    height: 504px;
    overflow: hidden;
    box-shadow: var(--card-shadow);
  }
  .card__face {
    position: absolute;
    left: 288px;
    top: 0;
    width: 504px;
    height: 288px;
    transform-origin: top left;
    transform: rotate(90deg);
  }

  /* Front: wood-grain face */
  .card--front .card__face {
    background: linear-gradient(170deg, var(--wood-light) 0%, var(--wood-mid) 40%, var(--wood-light) 70%, var(--wood-dark) 100%);
  }
  .brand {
    position: absolute;
    top: 104px;
    left: 72px;
    display: flex;
    align-items: center;
    gap: 12px;
  }
  .brand__mark {
    width: 18px;
    height: 18px;
    border-radius: 50%;
    background: var(--brand-blue);
  }
  .brand__name {
    font-family: "Questrial", sans-serif;
    font-size: 52px;
    font-weight: 400;
    color: var(--brand-blue);
    line-height: 1;
    white-space: nowrap;
  }
  .contact {
    position: absolute;
    left: 230px;
    top: 196px;
    list-style: none;
    font-family: "Source Sans 3", sans-serif;
    font-size: 14px;
    color: var(--ink);
    line-height: 1.3;
  }
  .contact__item {
    display: flex;
    align-items: center;
    gap: 7px;
    white-space: nowrap;
  }
  .contact__icon {
    width: 10px;
    height: 10px;
    flex: none;
  }
  .contact__item--indent { padding-left: 17px; }

  /* Back: product photo face */
  .card--back .card__photo {
    position: absolute;
    inset: 0;
    background: linear-gradient(135deg, var(--photo-cream) 0%, var(--photo-tan) 45%, var(--photo-salmon) 75%, var(--photo-tan) 100%);
  }
  .overlay-name {
    position: absolute;
    top: 104px;
    left: 70px;
    font-family: "Questrial", sans-serif;
    font-size: 56px;
    color: var(--overlay-white);
    line-height: 1;
    white-space: nowrap;
  }
  .web {
    position: absolute;
    left: 70px;
    top: 222px;
    font-family: "Source Sans 3", sans-serif;
    font-size: 16px;
    color: #ffffff;
    letter-spacing: 0.3px;
  }
</style>
</head>
<body>
<main class="sheet">

  <section class="card card--front" aria-label="Business card front">
    <div class="card__face" role="img" aria-label="Light oak wood grain surface">
      <div class="brand">
        <span class="brand__mark" aria-hidden="true"></span>
        <span class="brand__name">Reef Harvest</span>
      </div>

      <ul class="contact">
        <li class="contact__item">
          <svg class="contact__icon" viewBox="0 0 10 10" aria-hidden="true"><rect x="0.5" y="0.5" width="9" height="9" rx="1.5" fill="var(--ink)"/><path d="M3 2.5c0 3 1.5 4.5 4.5 4.8l.5-1.4-1.5-.6-.6.7C5 5.5 4.5 5 4.1 4.1l.7-.6-.6-1.5z" fill="#fff"/></svg>
          0000-000-000
        </li>
        <li class="contact__item">
          <svg class="contact__icon" viewBox="0 0 10 10" aria-hidden="true"><rect x="0.5" y="0.5" width="9" height="9" rx="1.5" fill="var(--ink)"/><path d="M2 3h6v4H2z M2 3l3 2.2L8 3" fill="none" stroke="#fff" stroke-width="0.8"/></svg>
          email@
        </li>
        <li class="contact__item">
          <svg class="contact__icon" viewBox="0 0 10 10" aria-hidden="true"><path d="M5 0.5a3.2 3.2 0 0 0-3.2 3.2C1.8 6 5 9.5 5 9.5S8.2 6 8.2 3.7A3.2 3.2 0 0 0 5 0.5z" fill="var(--ink)"/><circle cx="5" cy="3.7" r="1.2" fill="#fff"/></svg>
          7/212-238 Kellaway Rd
        </li>
        <li class="contact__item contact__item--indent">Palm Cove 4570</li>
      </ul>
    </div>
  </section>

  <section class="card card--back" aria-label="Business card back">
    <div class="card__face">
      <div class="card__photo" role="img" aria-label="Photo of pan-seared salmon fillets on a cream plate with sliced green jalapeño on a wooden table"></div>
      <p class="overlay-name">Reef Harvest</p>
      <p class="web">yourwebsite.com</p>
    </div>
  </section>

</main>
</body>
</html>
```